Willow Cradle Pregnancy and Baby Massage

I need a web design for a new business, WILLOW CRADLE PREGNANCY AND BABY MASSAGE that I am in the process of setting up in the suburbs of Perth, Western Australia. The business is owned and operated by myself and my intention is to service Pregnant Mothers and Parents of Young Babies that would benefit from massage. I would like to have a "Home Page" and pages for "About Me", "Pregnancy Massage", "Baby Massage", a Pricing Page for Pregnancy Massage Sessions, a Pricing Page for Baby Massage Sessions, and a "Contact Me" page to allow clients to either contact me with queries or book available pregnancy massage sessions on a particular day of the week. I would also like a "News" page that would include articles I have written, news about new courses and a link to my Community page (yet to be set up). I would like to keep the colour schemes similar to my logo design colours. I need the design to be easy to follow and to appeal to a younger audience (20's to mid 30's).
The target audience is pregnant mothers-to-be wishing to receive massage treatments, and new parents and grandparents of small babies that would like to learn how to massage their babies.
The look and feel should be modern, professional, elegant and feminine.
I need the design to be in a standard format such that I can update the content by myself ( and does not need specialised software) as the company and business progresses.

Target Market(s)

Contact Information for Business Card

Card should have rounded edges. Design should have the same "feel" as the website. Contact Details of my business address, mobile phone, email and website should be included.

Font styles to use
Script

Requirements
Must have
• Same colours as logo design. In cmyk system, the colours are: 20,60,0,0 which best result is pantone 681 and 40,40,0,0 which best result is pantone 2645. Card should include the logo design.

```html
<!DOCTYPE html>
<html lang="en">
<head>
<meta charset="utf-8">
<title>Willow Cradle Pregnancy and Baby Massage</title>
<link rel="stylesheet" href="https://fonts.googleapis.com/css2?family=Dancing+Script:wght@600;700&family=Open+Sans:wght@400;600&display=swap">
<style>
:root{
  --lavender:#8e7bb6;
  --orchid:#b0609f;
  --orchid-soft:#c07bb2;
  --heading:#a4579a;
  --ink:#444;
  --muted:#777;
  --light:#f2f2f2;
  --white:#fff;
  --line:#d6d6d6;
  --skin:linear-gradient(135deg,#f0e0d6,#dcbba8 60%,#cfd9e0);
}
*{box-sizing:border-box;margin:0;padding:0}
html,body{width:1200px;height:4215px;overflow:hidden}
body{font-family:"Open Sans",Arial,sans-serif;color:var(--ink);background:var(--white);font-size:15px;line-height:1.5}
.script{font-family:"Dancing Script",cursive;font-weight:700}
.btn{display:inline-block;background:var(--lavender);color:var(--white);font-size:17px;letter-spacing:.5px;text-transform:uppercase;padding:14px 32px}
.wordmark{font-family:"Dancing Script",cursive;font-weight:700;color:var(--heading);white-space:nowrap}

/* top bar */
.topbar{height:40px;border-bottom:1px solid var(--line);display:flex;align-items:center;padding-left:78px;font-size:13px}
.topbar .call{margin-right:30px}
.topbar .call b{color:var(--orchid);font-weight:400}
.topbar .social{margin-left:auto;display:flex;height:100%}
.topbar .social span{width:62px;border-left:1px solid var(--line);display:flex;align-items:center;justify-content:center}
.topbar .social i{width:14px;height:14px;border-radius:50%;background:#bbb;display:block}
.topbar .login{width:104px;border-left:1px solid var(--line);display:flex;align-items:center;justify-content:center;gap:8px}

/* nav */
.nav{height:106px;display:flex;align-items:center;padding:0 78px;border-bottom:1px solid var(--line)}
.nav .brand{display:flex;align-items:center;gap:10px}
.nav .brand .dot{width:26px;height:26px;border-radius:50%;background:var(--orchid)}
.nav .brand .wordmark{font-size:22px;line-height:1.1;display:block}
.nav .brand small{display:block;font-size:10px;color:var(--heading);white-space:nowrap}
.nav ul{list-style:none;display:flex;gap:16px;margin-left:auto;font-size:13.5px;white-space:nowrap}
.nav li.active{color:var(--orchid);border-bottom:2px solid var(--orchid);padding-bottom:4px}

/* hero */
.hero{position:relative;height:571px;background:linear-gradient(90deg,#ead9cc 0%,#efe9e6 40%,#e8e4e6 100%);text-align:center}
.hero .visual{position:absolute;inset:0}
.hero .content{position:relative;padding-top:120px}
.hero .mark{width:60px;height:60px;border-radius:50%;background:var(--orchid);margin:0 auto 18px}
.hero h1{font-size:74px;color:var(--orchid);line-height:1}
.hero h2{font-weight:400;font-size:30px;color:var(--lavender);margin:10px 0 30px}

/* welcome */
.welcome{height:449px;position:relative;padding:60px 0 0 78px}
.welcome h2{font-size:50px;color:var(--heading);line-height:1.1}
.welcome p{width:640px;font-size:15px;line-height:1.8;margin:16px 0 32px}
.welcome .photo{position:absolute;right:70px;top:30px;width:380px;height:390px;background:var(--skin)}

/* split panels */
.split{display:flex;height:576px}
.split .photo{width:600px;height:100%}
.split .panel{width:600px;height:100%;color:var(--white);padding:50px 40px}
.panel.lavender{background:var(--lavender)}
.panel.orchid{background:var(--orchid)}
.panel h2{font-size:50px;line-height:1.1}
.panel h3{font-size:26px;margin:22px 0 12px;font-family:"Dancing Script",cursive}
.panel p{font-size:14px;line-height:1.6}
.panel ul{list-style:none;font-size:13.5px;line-height:1.6}
.panel li:before{content:"• "}

/* session band */
.session{height:365px;background:linear-gradient(90deg,#f3e5e3,#faf5f4 50%,#f3e7e5);text-align:center;padding-top:55px}
.session h2{font-size:46px;color:var(--heading)}
.session p{width:940px;margin:18px auto 26px;font-size:14.5px;line-height:1.9}

/* baby sessions */
.sessions{height:619px;background:var(--light);text-align:center;padding-top:50px}
.sessions h2{font-size:48px;color:var(--heading)}
.cards{display:flex;justify-content:center;gap:70px;margin-top:36px}
.card{width:290px}
.card .photo{width:230px;height:200px;margin:0 auto;background:var(--skin)}
.card h3{font-weight:400;font-size:21px;color:var(--orchid);margin:20px 0 10px}
.card p{font-size:14px;line-height:1.6;margin-bottom:22px}

/* contact */
.contact{height:478px;position:relative;text-align:center;padding-top:50px}
.contact h2{font-size:50px;color:var(--heading)}
.form{width:360px;margin:18px auto 0;display:flex;flex-direction:column;gap:12px}
.field{height:42px;border:1px solid var(--line);display:flex;align-items:center;justify-content:space-between;padding:0 12px;font-size:13px;color:var(--muted)}
.field.msg{height:70px;align-items:flex-start;padding-top:10px}
.submit{width:188px;margin:12px auto 0;background:var(--orchid-soft);color:var(--white);padding:12px;font-size:16px}
.contact .photo{position:absolute;right:110px;top:25px;width:300px;height:430px;background:linear-gradient(180deg,#f3e6dc,#e8d2c0 50%,#f4f1ee)}

/* footer */
.footer{height:337px;background:var(--orchid);color:var(--white);display:flex;padding:60px 0 0 150px}
.footer .about{width:260px}
.footer .about .dot{width:46px;height:46px;border-radius:50%;background:var(--white);margin:0 0 10px 40px;opacity:.9}
.footer .about .wordmark{color:var(--white);font-size:30px;line-height:1.1;display:block}
.footer .about small{display:block;font-size:14px;font-weight:600;white-space:nowrap}
.footer .about p{font-size:13.5px;margin-top:10px}
.footer h4{font-weight:600;font-size:20px;margin-bottom:10px}
.footer .links{width:240px;margin-left:40px;font-size:13.5px;line-height:1.65}
.footer .info{width:300px;font-size:13.5px}
.footer .info div{display:flex;gap:12px;margin-bottom:10px}
.footer .follow{font-size:13.5px}
.footer .follow div{display:flex;align-items:center;gap:10px;margin-bottom:10px}
.footer .follow i{width:30px;height:30px;border-radius:50%;background:var(--white);display:block}
.bottom{height:98px;background:var(--orchid);border-top:1px solid rgba(255,255,255,.35);color:var(--white);display:flex;align-items:center;padding:0 110px 0 78px;font-size:14px}
.bottom .wordmark{color:var(--white);font-size:18px;margin-right:8px}
.bottom .sitemap{margin-left:auto}
</style>
</head>
<body>

<header class="topbar">
  <span class="call">Call us Today <b>(040 5550 173)</b></span>
  <span>maree@willowcradle.example</span>
  <div class="social">
    <span><i></i></span><span><i></i></span><span><i></i></span><span><i></i></span>
    <div class="login">Login
      <svg width="14" height="14" viewBox="0 0 14 14"><circle cx="7" cy="4" r="3" fill="none" stroke="#b0609f"/><path d="M1 13c1-4 11-4 12 0" fill="none" stroke="#b0609f"/></svg>
    </div>
  </div>
</header>

<nav class="nav">
  <div class="brand"><span class="dot"></span><div><span class="wordmark">Willow Cradle</span><small>Pregnancy and Baby Massage</small></div></div>
  <ul>
    <li class="active">Home</li><li>About Me</li><li>Pregnancy Massage</li><li>Baby Massage</li><li>Pregnancy Massage Sessions</li><li>Baby Massage Sessions</li><li>Contact us</li>
  </ul>
</nav>

<section class="hero">
  <div class="visual" role="img" aria-label="Photo of a pregnant woman relaxing during a massage on white towels"></div>
  <div class="content">
    <div class="mark"></div>
    <h1 class="script">Willow Cradle</h1>
    <h2>Pregnancy and Baby Massage</h2>
    <span class="btn">Contact Us</span>
  </div>
</section>

<section class="welcome">
  <h2 class="script">Welcome to Willow Cradle</h2>
  <p>Willow Cradle Pregnancy and Baby Massage was launched in 2017, offering massage for pregnant women, and instruction of baby massage to parents, grandparents and carers. My vision is to provide a professional massage service to pregnant mothers and babies that also benefits from my skills and experience as a midwife. My expectation is that after each session, my clients should leave feeling relaxed, calm, emotionally nurtured, soothed and supported. At all times, I will take the utmost care of your privacy, safety and comfort in what is a very personal, intimate time in your life.</p>
  <span class="btn">Learn More</span>
  <div class="photo" role="img" aria-label="Photo of cupped hands holding a framed picture of a sleeping newborn"></div>
</section>

<section class="split">
  <div class="photo" role="img" aria-label="Photo of a pregnant woman lying on her side receiving a back massage" style="background:linear-gradient(135deg,#e8ded8,#d9c3b6 60%,#cdd6dc)"></div>
  <div class="panel lavender">
    <h2 class="script">Pregnancy Massage</h2>
    <p>Pregnancy massage is the prenatal use of massage therapy to support the physiological, structural and emotional wellbeing of both mother and baby.</p>
    <h3>Benefits of Pregnancy Massage</h3>
    <ul>
      <li>Reduces anxiety caused by hormonal changes</li>
      <li>Improves circulation</li>
      <li>Reduces muscle aches and pain; muscle and joint conditions such as backache, shoulder and neck pain, hip pain, leg cramps, oedema and carpal tunnel</li>
      <li>Relaxes tense muscle, tones loose muscle and increases muscle flexibility</li>
      <li>Enhances vitality and energy</li>
      <li>Reduces fatigue</li>
      <li>Enhances relaxation and improves sleep patterns as it helps to soothe and relax nervous tension</li>
      <li>Increases circulation to the skin</li>
    </ul>
  </div>
</section>

<section class="split">
  <div class="panel orchid">
    <h2 class="script">Baby Massage</h2>
    <p>"Being touched and caressed, being massaged, is food for the infant. Food as necessary as minerals, vitamins, and proteins."</p>
    <h3>Benefits of Pregnancy Massage</h3>
    <ul>
      <li>Relaxation of skeletal muscles</li>
      <li>Strengthens the immune system</li>
      <li>Reduces stress hormone levels in children and parents</li>
      <li>Improves sleep and regulates sleep patterns</li>
      <li>Relieves discomfort of wind, constipation, colic and reflux, sinus and chest congestion</li>
      <li>Reduces crying</li>
      <li>Enhances attachment and bonding</li>
      <li>Reduces symptoms of eczema</li>
      <li>Enhances emotions and improves mood</li>
      <li>Improves digestive, respiratory and circulatory system</li>
      <li>Reduces postnatal depression</li>
      <li>Reduces anxiety</li>
      <li>Increases blood and lymphatic circulation</li>
      <li>Enhances cognitive and motor development</li>
    </ul>
  </div>
  <div class="photo" role="img" aria-label="Photo of hands gently massaging a baby lying on a blue towel" style="background:linear-gradient(135deg,#f1e4dc,#e6c7b5 55%,#c9dbe6)"></div>
</section>

<section class="session">
  <h2 class="script">Pregnancy Massage Session</h2>
  <p>Each session begins with a consultation to assess any high-risk factors, and to review any changes the body has undergone since the last session. This way the massage can be given in a safe manner. Each session begins with a consultation to assess any high-risk factors, and to review any changes the body has undergone since the last session. This way the massage can be given in a safe manner.</p>
  <span class="btn">Learn More Detail</span>
</section>

<section class="sessions">
  <h2 class="script">Baby Massage Sessions</h2>
  <div class="cards">
    <div class="card">
      <div class="photo" role="img" aria-label="Framed photo of a sleeping newborn"></div>
      <h3>Colic relief course</h3>
      <p>Lorem Ipsum is simply dummy text of the printing and typesetting industry. Lorem Ipsum has been the industry's standard dummy text ever since the</p>
      <span class="btn">More Detail</span>
    </div>
    <div class="card">
      <div class="photo" role="img" aria-label="Framed photo of a baby wrapped in a blanket"></div>
      <h3>Ante Natal Session</h3>
      <p>Lorem Ipsum is simply dummy text of the printing and typesetting industry. Lorem Ipsum has been the industry's standard dummy text ever since the</p>
      <span class="btn">More Detail</span>
    </div>
    <div class="card">
      <div class="photo" role="img" aria-label="Framed photo of a baby being massaged"></div>
      <h3>Advanced Baby Massage</h3>
      <p>Lorem Ipsum is simply dummy text of the printing and typesetting industry. Lorem Ipsum has been the industry's standard dummy text ever since the</p>
      <span class="btn">More Detail</span>
    </div>
  </div>
</section>

<section class="contact">
  <h2 class="script">Contact Us</h2>
  <div class="form">
    <div class="field">Name<svg width="14" height="14" viewBox="0 0 14 14"><circle cx="7" cy="4" r="3" fill="none" stroke="#888"/><path d="M1 13c1-4 11-4 12 0" fill="none" stroke="#888"/></svg></div>
    <div class="field">Phone<svg width="14" height="14" viewBox="0 0 14 14"><path d="M3 1l3 3-2 2c1 2 2 3 4 4l2-2 3 3-2 2C6 13 1 8 1 3z" fill="none" stroke="#888"/></svg></div>
    <div class="field">Email<svg width="16" height="12" viewBox="0 0 16 12"><rect x="1" y="1" width="14" height="10" fill="none" stroke="#888"/><path d="M1 1l7 6 7-6" fill="none" stroke="#888"/></svg></div>
    <div class="field msg">Message<svg width="14" height="14" viewBox="0 0 14 14"><rect x="1" y="2" width="10" height="11" fill="none" stroke="#888"/><path d="M6 8l7-7" stroke="#888"/></svg></div>
    <div class="submit">SUBMIT</div>
  </div>
  <div class="photo" role="img" aria-label="Photo of a smiling mother lifting her baby overhead"></div>
</section>

<footer class="footer">
  <div class="about">
    <div class="dot"></div>
    <span class="wordmark">Willow Cradle</span>
    <small>Pregnancy and Baby Massage</small>
    <p>Lorem Ipsum is simply dummy text of the printing and typesetting industry. Lorem Ipsum has been the industry's</p>
  </div>
  <div class="links">
    <h4>Useful Link</h4>
    Home<br>About Me<br>Pregnancy Massage<br>Baby Message<br>Pregnancy Massage Sessions<br>Baby Massage Sessions<br>Contact
  </div>
  <div class="info">
    <h4>Contact Info</h4>
    <div><svg width="14" height="18" viewBox="0 0 14 18"><path d="M7 17C2 10 1 8 1 6a6 6 0 0112 0c0 2-1 4-6 11z" fill="#fff"/><circle cx="7" cy="6" r="2" fill="#b0609f"/></svg><span>Maree Colton<br>Willow Cradle Pregnancy and<br>Infant Massage</span></div>
    <div><svg width="14" height="14" viewBox="0 0 14 14"><path d="M3 1l3 3-2 2c1 2 2 3 4 4l2-2 3 3-2 2C6 13 1 8 1 3z" fill="#fff"/></svg><span>040 5550 173</span></div>
    <div><svg width="16" height="12" viewBox="0 0 16 12"><rect x="1" y="1" width="14" height="10" fill="none" stroke="#fff"/><path d="M1 1l7 6 7-6" fill="none" stroke="#fff"/></svg><span>maree@willowcradle.example</span></div>
    <div><svg width="14" height="14" viewBox="0 0 14 14"><circle cx="7" cy="7" r="6" fill="none" stroke="#fff"/><path d="M1 7h12M7 1v12" stroke="#fff"/></svg><span>www.willowcradle.example</span></div>
  </div>
  <div class="follow">
    <h4>Follow us on</h4>
    <div><i></i>Community</div>
    <div><i></i>Updates</div>
    <div><i></i>Network</div>
    <div><i></i>Gallery</div>
  </div>
</footer>
<div class="bottom">
  <span class="wordmark">Willow Cradle</span> | Copyright 2017. All Rights Reserved
  <span class="sitemap">Site Map</span>
</div>

</body>
</html>
```